Law Firm Business Card

This is a business card for a law firm that serves US military and veterans.

The card must have ONLY the following (we want an uncluttered look):

- Company logo (PNG, GIF, JPEG copies uploaded)
- A tagline reading: "a law firm for service members and veterans"
- My name and title: "Tobias Marlow" and "Attorney"
- My email: "tobias.marlow@brinmoorlegal.com"
- My number: "855-FIRM-ONE (347-6663)"

We are looking for a clean, simple layout with only the above information, likely printed on a bright white cotton stock. The font of our logo is DIN 1451, and the font used on our website is Helvetica Neue. The color of our logo is #336699, and we probably want the tagline in that color also, and my contact information in a dark grey. Please review our website at www.brinmoorlegal.com to ensure your card design complements our website style.

Thanks and we look forward to seeing your submissions.

A few notes:

- Two-sided submissions are ok
- Please don't add graphics (scales of justice, judges hammer, etc)

```html
<!DOCTYPE html>
<html lang="en">
<head>
<meta charset="utf-8">
<title>Brinmoor Legal — Business Card</title>
<link rel="stylesheet" href="https://fonts.googleapis.com/css2?family=Barlow+Condensed:wght@600&family=Barlow:wght@500;600&family=Crimson+Pro:ital,wght@0,500;1,600&display=swap">
<style>
  :root {
    --brand-blue: #2b6bc9;
    --faint-blue: #e6ecf6;
    --ink: #2a2a2a;
    --band-grey: #6e7777;
    --card-white: #ffffff;
    --stage: #eceef1;
  }
  html, body {
    margin: 0;
    width: 1200px;
    height: 526px;
    overflow: hidden;
    background: var(--stage);
  }
  .stage {
    position: relative;
    width: 1200px;
    height: 526px;
  }
  .card {
    position: absolute;
    top: 118px;
    width: 500px;
    height: 290px;
    overflow: hidden;
    box-shadow: 0 6px 18px rgba(0,0,0,0.18);
  }
  .card--front { left: 60px; background: var(--card-white); }
  .card--back  { left: 640px; background: var(--brand-blue); }

  /* Front */
  .wordmark {
    position: absolute;
    left: 30px;
    top: 34px;
    margin: 0;
    font-family: "Barlow Condensed", sans-serif;
    font-weight: 600;
    font-size: 46px;
    line-height: 1;
    letter-spacing: 1px;
    text-transform: uppercase;
    color: var(--brand-blue);
  }
  .faint-block {
    position: absolute;
    right: 50px;
    top: 40px;
    width: 120px;
    height: 190px;
    background: var(--faint-blue);
  }
  .contact {
    position: absolute;
    left: 30px;
    top: 150px;
    font-family: "Barlow", sans-serif;
    color: var(--ink);
  }
  .contact__name {
    margin: 0 0 10px;
    font-size: 15px;
    font-weight: 600;
    color: var(--brand-blue);
  }
  .contact__title { font-size: 12px; color: var(--ink); }
  .contact__list { list-style: none; margin: 0; padding: 0; }
  .contact__item {
    display: flex;
    align-items: center;
    gap: 8px;
    font-size: 12.5px;
    font-weight: 500;
    margin-bottom: 5px;
  }
  .contact__icon { width: 12px; height: 12px; flex: none; }
  .front-tagline {
    position: absolute;
    left: 30px;
    top: 238px;
    margin: 0;
    font-family: "Crimson Pro", serif;
    font-weight: 500;
    font-size: 15px;
    color: var(--brand-blue);
  }
  .front-bands { position: absolute; left: 0; bottom: 0; }

  /* Back */
  .back-name {
    position: absolute;
    left: 40px;
    top: 95px;
    margin: 0;
    font-family: "Barlow Condensed", sans-serif;
    font-weight: 600;
    font-size: 44px;
    line-height: 1.05;
    text-transform: uppercase;
    color: var(--card-white);
  }
  .back-copy {
    position: absolute;
    left: 210px;
    top: 70px;
    width: 270px;
    text-align: center;
    font-family: "Crimson Pro", serif;
    color: var(--card-white);
  }
  .back-copy__tagline {
    margin: 0 0 14px;
    font-weight: 500;
    font-size: 24px;
    line-height: 1.15;
  }
  .back-copy__url {
    margin: 0;
    font-style: italic;
    font-weight: 600;
    font-size: 17px;
  }
</style>
</head>
<body>
<main class="stage">

  <section class="card card--front" aria-label="Business card front">
    <div class="faint-block" aria-hidden="true"></div>
    <h1 class="wordmark">Brinmoor Legal</h1>

    <div class="contact">
      <p class="contact__name">Tobias Marlow<span class="contact__title">, Attorney</span></p>
      <ul class="contact__list">
        <li class="contact__item">
          <svg class="contact__icon" viewBox="0 0 12 12" aria-hidden="true"><circle cx="6" cy="6" r="5.3" fill="none" stroke="#2a2a2a" stroke-width="1"/><path d="M4 3.2l1.2 1.4-0.6 0.8c0.4 0.9 1 1.5 1.9 1.9l0.8-0.6 1.4 1.2-0.7 0.9C6 8.6 3.4 6 3.3 3.9z" fill="#2a2a2a"/></svg>
          855-FIRM-ONE (347-6663)
        </li>
        <li class="contact__item">
          <svg class="contact__icon" viewBox="0 0 12 12" aria-hidden="true"><rect x="1" y="2.5" width="10" height="7" rx="1" fill="#2a2a2a"/><path d="M1.5 3l4.5 3.5L10.5 3" fill="none" stroke="#fff" stroke-width="1"/></svg>
          tobias.marlow@brinmoorlegal.com
        </li>
        <li class="contact__item">
          <svg class="contact__icon" viewBox="0 0 12 12" aria-hidden="true"><circle cx="6" cy="6" r="5" fill="none" stroke="#2a2a2a" stroke-width="1"/><ellipse cx="6" cy="6" rx="2.2" ry="5" fill="none" stroke="#2a2a2a" stroke-width="0.8"/><path d="M1 6h10" stroke="#2a2a2a" stroke-width="0.8"/></svg>
          www.brinmoorlegal.com
        </li>
      </ul>
    </div>

    <p class="front-tagline">A Law Firm For Service Members And Veterans</p>

    <svg class="front-bands" width="500" height="50" viewBox="0 0 500 50" aria-hidden="true">
      <polygon points="262,22 500,8 500,26 250,26" fill="var(--brand-blue)"/>
      <polygon points="0,26 252,26 236,50 0,50" fill="var(--band-grey)"/>
      <polygon points="252,26 500,26 500,50 236,50" fill="#ffffff"/>
    </svg>
  </section>

  <section class="card card--back" aria-label="Business card back">
    <p class="back-name">Brinmoor<br>Legal</p>
    <div class="back-copy">
      <p class="back-copy__tagline">A Law Firm<br>For Service<br>Members &amp; Veterans</p>
      <p class="back-copy__url">www.brinmoorlegal.com</p>
    </div>
  </section>

</main>
</body>
</html>
```